Basic / Quick Business Card

Quick easy design project!

Need a one sided basic business card that matches font & style of brand and bottle label for our gourmet condiment, Brindle Harrow Sauce. Brindle Harrow Sauce is sold in specialty retail, gourmet groceries and appears on chef-driven restaurant menus, so the target market is a high end, gourmet, artisan-made food-loving customer.

Files Included:
Sauce Bottle Label
Brindle Harrow Sauce Round Logos

**About the logos - the logo may be used in a circle or alone vertically as on side of the bottle label**

Layout of Card:
May be vertical or horizontal based on designer ideas.

Logo usage (in circle vs. stand alone vertical logo) is up to designers descretion as well.

Reverse side of business card will be various high end / professional product photos / food shots using us.kelbo.com system. **Designer on this project will NOT design a reserve for the card.**

Paper that will be used for printing:
Kelbo Standard - it's a WHITE paper, but we use a cream background on Brindle Harrow Sauce branding, so please take this into account on design to stay brand consistent.

Elements & Copy for Card:
1. Logo in either script horizontal or vertical version
2. Copy: "Artisan Made - Small Batch"
3. Name - Wes Dorrance
4. Title - Creator
5. Phone - xxx.xxx.xxxx
6. xxxx@brindleharrow.com
7. URL: brindleharrowsauce.com
8. Social Media: @getbrindleharrow on Quillo / Pagora / Lumigrid

Please provide final files in Illustrator or InDesign format.

```html
<!DOCTYPE html>
<html lang="en">
<head>
<meta charset="utf-8">
<title>Brindle Harrow Sauce – Business Card</title>
<link rel="stylesheet" href="https://fonts.googleapis.com/css2?family=Courier+Prime:wght@400;700&display=swap">
<style>
  :root {
    --backdrop: #f1f0ec;
    --card-black: #231f20;
    --brand-yellow: #f6c200;
    --brand-red: #d7261e;
    --brand-cream: #f2f0c2;
    --brand-gold: #e6a623;
    --brand-green: #1f3b2f;
    --paper-white: #ffffff;
  }
  html, body {
    margin: 0;
    padding: 0;
    width: 1200px;
    height: 926px;
    overflow: hidden;
    background: var(--backdrop);
  }
  .canvas {
    position: relative;
    width: 1200px;
    height: 926px;
  }
  .business-card {
    position: absolute;
    left: 80px;
    top: 167px;
    width: 1040px;
    height: 591px;
    box-shadow: 0 10px 30px rgba(0,0,0,0.18);
  }
  .business-card text {
    font-family: "Courier Prime", "Courier New", monospace;
  }
  .tagline { fill: var(--paper-white); font-weight: 700; font-size: 15px; }
  .person-name { fill: var(--card-black); font-weight: 700; font-size: 20px; }
  .person-title { fill: var(--card-black); font-weight: 700; font-size: 12.5px; }
  .contact-line { fill: var(--brand-yellow); font-size: 9px; }
  .web-address { fill: var(--card-black); font-size: 10.5px; }
  .social-handle { fill: var(--brand-yellow); font-size: 8px; }
  .social-networks { fill: var(--paper-white); font-size: 7px; }
  .brand-name { fill: var(--brand-green); font-weight: 700; font-size: 26px; }
</style>
</head>
<body>
<main class="canvas">
  <svg class="business-card" viewBox="0 0 510 290" xmlns="http://www.w3.org/2000/svg" role="group" aria-label="Brindle Harrow Sauce business card for Wes Dorrance">
    <!-- card ground -->
    <rect class="card-ground" x="0" y="0" width="510" height="290" fill="var(--card-black)"/>

    <!-- tagline -->
    <text class="tagline" x="25" y="35">Artisan Made - Small Batch</text>

    <!-- name banner -->
    <path class="name-banner" d="M0 58 H190 L234 115.5 L190 173 H0 Z" fill="var(--brand-yellow)" stroke="var(--paper-white)" stroke-width="2.5"/>
    <text class="person-name" x="99" y="120" text-anchor="middle">Wes Dorrance</text>
    <text class="person-title" x="99" y="140" text-anchor="middle">Creator</text>

    <!-- dashed pointer to web address -->
    <path class="pointer-line" d="M34 178 C40 225 120 215 180 205 C230 197 262 205 264 236" fill="none" stroke="var(--brand-yellow)" stroke-width="2" stroke-dasharray="5 3"/>
    <path class="pointer-head" d="M256 229 L264 241 L272 229" fill="none" stroke="var(--brand-yellow)" stroke-width="2" stroke-dasharray="4 2"/>

    <!-- brand seal -->
    <circle class="brand-seal" cx="394" cy="143" r="96" fill="var(--brand-cream)" stroke="var(--brand-gold)" stroke-width="5"/>
    <text class="brand-name" x="394" y="120" text-anchor="middle">Brindle</text>
    <text class="brand-name" x="394" y="150" text-anchor="middle">Harrow</text>
    <text class="brand-name" x="394" y="180" text-anchor="middle">Sauce</text>

    <!-- footer -->
    <rect class="footer-rule" x="0" y="247" width="510" height="4" fill="var(--brand-red)"/>
    <rect class="footer-web-box" x="170" y="251" width="170" height="39" fill="var(--brand-yellow)"/>

    <text class="contact-line" x="14" y="268">Phone - xxx.xxx.xxxx</text>
    <text class="contact-line" x="14" y="279">xxxx@brindleharrow.com</text>

    <text class="web-address" x="255" y="274" text-anchor="middle">brindleharrowsauce.com</text>

    <text class="social-handle" x="425" y="268" text-anchor="middle" textLength="156" lengthAdjust="spacingAndGlyphs">social media: @getbrindleharrow</text>
    <text class="social-networks" x="425" y="279" text-anchor="middle">on quillo / pagora / lumigrid</text>
  </svg>
</main>
</body>
</html>
```